Oil Field Service company needs professional business cards

Looking to clean up our current company business cards and look a little more professional. Brenwick Casing Services is a US based company that services the oil field. We deal with engineers, managers and oil rigs....................................................................................................................................................................................................................................................................................................................................................................................................

Target Market(s)

Oil and Gas professionals

Industry/Entity Type

Oil And Gas

Contact Information for Business Card

See attached photo as example

Font styles to use
Sans Serif

Colors
ec1f27

Requirements
Must have
• Company Logo, Name, Title, Cell, Office, Fax, Email.
• See attached photo
Nice to have
• External CRT, Internal CRT, Casing Crews, Torque Turn, Laydown Machine
Should not have
• Do not introduce any new pictures and keep it professional looking

```html
<!DOCTYPE html>
<html lang="en">
<head>
<meta charset="utf-8">
<title>Brenwick Casing Services – Business Card</title>
<link rel="stylesheet" href="https://fonts.googleapis.com/css2?family=Montserrat:wght@800&family=Oswald:wght@300;400&family=Roboto:wght@400;500;700&display=swap">
<style>
  :root {
    --brand-red: #ec1f27;
    --band-red: #d3222a;
    --slate: #3d5366;
    --ink: #3a3a3a;
    --muted: #555555;
    --card: #f7f7f7;
    --backdrop: #e4e4e4;
  }
  * { margin: 0; padding: 0; box-sizing: border-box; }
  html, body { width: 1200px; height: 576px; overflow: hidden; }
  body { background: var(--backdrop); position: relative; font-family: "Roboto", sans-serif; }

  .card {
    position: absolute;
    top: 139px;
    width: 484px;
    height: 293px;
    background: var(--card);
    border-radius: 6px;
    box-shadow: 0 2px 5px rgba(0,0,0,0.18);
    overflow: hidden;
  }
  .card--front { left: 82px; }
  .card--back { left: 602px; }

  .brand-name {
    position: absolute;
    color: var(--slate);
    font-family: "Montserrat", sans-serif;
    font-weight: 800;
    text-align: center;
    line-height: 1;
  }
  .brand-name__main { display: block; }
  .brand-name__sub { display: block; letter-spacing: 0.16em; }

  .card--front .brand-name { left: 0; right: 0; top: 80px; }
  .card--front .brand-name__main { font-size: 56px; letter-spacing: 0.01em; }
  .card--front .brand-name__sub { font-size: 17px; margin-top: 26px; }

  .service-band {
    position: absolute;
    left: 0; right: 0; top: 220px;
    height: 26px;
    background: var(--band-red);
    color: #fff;
    font-weight: 500;
    font-size: 13px;
    display: flex;
    align-items: center;
    justify-content: center;
    gap: 8px;
    letter-spacing: 0.02em;
  }
  .service-band__divider { opacity: 0.9; }

  .front-web {
    position: absolute;
    left: 0; right: 0; top: 262px;
    display: flex;
    align-items: center;
    justify-content: center;
    gap: 10px;
    font-size: 13px;
    color: var(--ink);
  }
  .front-web__rule { width: 66px; height: 2px; background: var(--brand-red); }

  .card--back .brand-name { left: 22px; width: 220px; top: 30px; }
  .card--back .brand-name__main { font-size: 40px; }
  .card--back .brand-name__sub { font-size: 13px; margin-top: 18px; }

  .holder {
    position: absolute;
    left: 22px; top: 160px;
  }
  .holder__name {
    font-family: "Oswald", sans-serif;
    font-weight: 400;
    font-size: 22px;
    color: var(--brand-red);
    line-height: 1.1;
  }
  .holder__title { font-size: 11.5px; color: var(--muted); margin-top: 2px; }

  .service-list {
    position: absolute;
    left: 22px; top: 229px;
    list-style: none;
    font-family: "Oswald", sans-serif;
    font-weight: 300;
    font-size: 12px;
    color: var(--ink);
    display: grid;
    grid-template-columns: auto auto;
    column-gap: 6px;
    row-gap: 2px;
    width: 180px;
  }
  .service-list li::before { content: "» "; }

  .contact-list {
    position: absolute;
    left: 280px; top: 168px;
    list-style: none;
    font-family: "Oswald", sans-serif;
    font-weight: 300;
    font-size: 12px;
    color: var(--ink);
  }
  .contact-list li { display: flex; align-items: center; height: 15.8px; }
  .contact-list svg { width: 10px; height: 10px; margin-right: 9px; fill: var(--brand-red); flex: none; }
</style>
</head>
<body>

<section class="card card--front" aria-label="Card front">
  <h1 class="brand-name">
    <span class="brand-name__main">BRENWICK</span>
    <span class="brand-name__sub">CASING SERVICES</span>
  </h1>
  <div class="service-band">
    <span>LAYDOWN MACHINE</span><span class="service-band__divider">|</span>
    <span>CASING CREW</span><span class="service-band__divider">|</span>
    <span>MUD TOOL</span><span class="service-band__divider">|</span>
    <span>TORQUE TURN</span>
  </div>
  <div class="front-web">
    <span class="front-web__rule"></span>
    <span>www.brenwickcs.com</span>
    <span class="front-web__rule"></span>
  </div>
</section>

<section class="card card--back" aria-label="Card back">
  <h2 class="brand-name">
    <span class="brand-name__main">BRENWICK</span>
    <span class="brand-name__sub">CASING SERVICES</span>
  </h2>

  <div class="holder">
    <p class="holder__name">Cole Harrington</p>
    <p class="holder__title">Area Manager</p>
  </div>

  <ul class="service-list">
    <li>Laydown Machine</li>
    <li>Casing Crew</li>
    <li>Mud Tool</li>
    <li>Torque Turn</li>
  </ul>

  <ul class="contact-list">
    <li>
      <svg viewBox="0 0 10 10" aria-hidden="true"><path d="M2 0.5h6v9H2z M3 1.5v6h4v-6z"/></svg>
      (555) 214-5700
    </li>
    <li>
      <svg viewBox="0 0 10 10" aria-hidden="true"><path d="M0.5 3.5 C2 1 8 1 9.5 3.5 L8 4.5 L7 3.2 H3 L2 4.5Z M2 5h6l1 4H1z"/></svg>
      (555) 318-7496
    </li>
    <li>
      <svg viewBox="0 0 10 10" aria-hidden="true"><path d="M2.5 0.5h5v2.5h-5z M0.5 3.5h9v4h-2v2h-5v-2h-2z M3.5 6v2.5h3V6z"/></svg>
      (555) 214-3230
    </li>
    <li>
      <svg viewBox="0 0 10 10" aria-hidden="true"><path d="M5 0.3a3.3 3.3 0 0 1 3.3 3.3C8.3 6 5 9.7 5 9.7S1.7 6 1.7 3.6A3.3 3.3 0 0 1 5 0.3z M5 2.3a1.3 1.3 0 1 0 0 2.6a1.3 1.3 0 1 0 0-2.6z"/></svg>
      Marlow Creek, OK 73000
    </li>
    <li>
      <svg viewBox="0 0 10 10" aria-hidden="true"><path d="M0.5 2h9v0.8L5 5.6 0.5 2.8z M0.5 3.8 5 6.6 9.5 3.8V8h-9z"/></svg>
      coleharrington@brenwickcs.com
    </li>
    <li>
      <svg viewBox="0 0 10 10" aria-hidden="true"><path d="M5 0.5a4.5 4.5 0 1 0 0 9a4.5 4.5 0 1 0 0-9z M5 1.6c-0.8 0.8-1.2 2-1.3 2.9h2.6C6.2 3.6 5.8 2.4 5 1.6z M1.6 5.5c0.2 1.4 1.2 2.5 2.5 2.9-0.5-0.8-0.8-1.9-0.9-2.9z M6.8 5.5c-0.1 1-0.4 2.1-0.9 2.9 1.3-0.4 2.3-1.5 2.5-2.9z"/></svg>
      www.brenwickcs.com
    </li>
  </ul>
</section>

</body>
</html>
```